Investment company needing business card

We are wanting a business card which looks sharp and easy on the eye. We are thinking of having a business card with the logo embossed on it, to really make it stand out. We will only have a small amount of information of the business card, person's name, position, email address and phone number

Contact Information for Business Card

Danielle Frost
Executive Assistant
+64 21 473 5162
danielf@harwickpartners.co.nz

Requirements
Must have
• Embossed logo
Should not have
• Not to be busy

```html
<!DOCTYPE html>
<html lang="en">
<head>
<meta charset="utf-8">
<title>Harwick Partners — Business Card</title>
<link rel="stylesheet" href="https://fonts.googleapis.com/css2?family=Exo+2:wght@700&family=Lato:wght@400&display=swap">
<style>
  :root {
    --backdrop: #b5b5b5;
    --card: #1e1d1e;
    --accent: #2dbd6e;
    --text-light: #d9d9d9;
    --emboss: #3a393b;
  }
  * { margin: 0; padding: 0; box-sizing: border-box; }
  html, body { width: 1200px; height: 802px; overflow: hidden; }
  body { background: var(--backdrop); position: relative; font-family: "Lato", sans-serif; }

  .card {
    position: absolute;
    top: 274px;
    width: 444px;
    height: 265px;
    background: var(--card);
  }
  .card--front { left: 134px; }
  .card--back { left: 624px; }

  .brand {
    position: absolute;
    display: flex;
    align-items: center;
    font-family: "Exo 2", sans-serif;
    font-weight: 700;
    text-transform: uppercase;
    white-space: nowrap;
  }
  .brand__mark { display: block; flex: none; }

  .card--front .brand {
    right: 26px;
    top: 60px;
    gap: 10px;
    color: var(--accent);
    font-size: 19px;
    letter-spacing: 0.3px;
  }
  .card--front .brand__mark { width: 40px; height: 40px; background: var(--accent); }

  .card--back .brand {
    left: 50%;
    top: 50%;
    transform: translate(-50%, -50%);
    gap: 14px;
    color: var(--emboss);
    font-size: 29px;
    letter-spacing: 0.5px;
  }
  .card--back .brand__mark { width: 62px; height: 62px; background: var(--emboss); }

  .contact-bar {
    position: absolute;
    left: 0;
    top: 153px;
    width: 8px;
    height: 89px;
    background: var(--accent);
  }
  .person {
    position: absolute;
    left: 28px;
    top: 156px;
  }
  .person__name {
    font-family: "Exo 2", sans-serif;
    font-weight: 700;
    font-size: 18px;
    line-height: 20px;
    color: var(--accent);
    text-transform: uppercase;
    letter-spacing: 0.2px;
  }
  .person__role {
    font-size: 12.5px;
    line-height: 16px;
    color: var(--text-light);
  }
  .person__details { margin-top: 12px; list-style: none; }
  .person__details li {
    display: flex;
    align-items: center;
    gap: 5px;
    font-size: 12.5px;
    line-height: 16px;
    color: var(--text-light);
  }
  .person__details svg { width: 10px; height: 10px; flex: none; }
</style>
</head>
<body>
  <section class="card card--front" aria-label="Business card front">
    <div class="brand">
      <span class="brand__mark"></span>
      <span class="brand__name">Harwick Partners</span>
    </div>
    <div class="contact-bar"></div>
    <div class="person">
      <p class="person__name">Danielle Frost</p>
      <p class="person__role">Executive Assistant</p>
      <ul class="person__details">
        <li>
          <svg viewBox="0 0 10 10" aria-hidden="true"><path fill="var(--accent)" d="M1 3.2C1 2 2.6 1.4 5 1.4S9 2 9 3.2V4H7V3.1H3V4H1Z M2.2 4.6h5.6L8.6 8.6H1.4Z"/></svg>
          <span>+64 21 473 5162</span>
        </li>
        <li>
          <svg viewBox="0 0 10 10" aria-hidden="true"><rect x="1" y="2.2" width="8" height="5.8" fill="var(--accent)"/><path d="M1.3 2.6 5 5.6 8.7 2.6" fill="none" stroke="var(--card)" stroke-width="0.9"/></svg>
          <span>danielf@harwickpartners.co.nz</span>
        </li>
      </ul>
    </div>
  </section>

  <section class="card card--back" aria-label="Business card back">
    <div class="brand">
      <span class="brand__mark"></span>
      <span class="brand__name">Harwick Partners</span>
    </div>
  </section>
</body>
</html>
```